New bussiness card, using company logo.
Lionel Brisk
Manager/Director
Brisk Property Developments
Po Box 5347
Thuringowa Central
Qld
0491 638 205
lionel@briskpropertydevelopments
eye catching, vibrant colours, professional

```html
<!DOCTYPE html>
<html lang="en">
<head>
<meta charset="utf-8">
<title>Brisk Property Developments – Business Cards</title>
<link rel="stylesheet" href="https://fonts.googleapis.com/css2?family=Open+Sans:wght@400;600;700;800&family=Exo+2:wght@500&display=swap">
<style>
  :root {
    --backdrop: #5e3420;
    --paper: #ffffff;
    --brand-red: #e0232f;
    --brand-green: #6cbd45;
    --brand-green-light: #8cc63f;
    --ink: #2b2b2b;
    --rule: #b9b9b9;
  }
  * { box-sizing: border-box; margin: 0; padding: 0; }
  html, body { width: 1200px; height: 746px; overflow: hidden; }
  body {
    background: var(--backdrop);
    font-family: "Open Sans", Arial, sans-serif;
    position: relative;
  }
  .card {
    position: absolute;
    width: 524px;
    height: 298px;
    overflow: hidden;
    box-shadow: 0 3px 8px rgba(0,0,0,.35);
  }
  .card--front { left: 47px; top: 36px; background: var(--paper); }
  .card--back-white { left: 611px; top: 40px; background: var(--paper); }
  .card--back-green { left: 48px; top: 394px; background: linear-gradient(160deg, var(--brand-green) 0%, var(--brand-green-light) 100%); }
  .card--back-red { left: 627px; top: 394px; background: var(--brand-red); }

  /* wordmark: invented name, single colour & weight, one plain square */
  .wordmark { position: absolute; display: flex; align-items: center; gap: 10px; font-weight: 800; white-space: nowrap; }
  .wordmark__square { flex: none; }
  .wordmark__name { line-height: 1.1; }

  .card--front .wordmark { left: 26px; top: 112px; color: var(--brand-red); font-size: 20px; white-space: normal; width: 235px; }
  .card--front .wordmark__square { width: 14px; height: 14px; background: var(--brand-green); }

  .divider { position: absolute; left: 265px; top: 66px; width: 1px; height: 144px; background: var(--rule); }

  .contact { position: absolute; left: 274px; top: 68px; color: var(--ink); }
  .contact__name { color: var(--brand-red); font-size: 19px; font-weight: 600; line-height: 1.2; }
  .contact__role { color: var(--brand-green); font-size: 14.5px; line-height: 1.3; margin-bottom: 12px; }
  .contact__row { display: flex; align-items: flex-start; gap: 6px; font-size: 13.5px; line-height: 1.35; margin-bottom: 6px; }
  .contact__row--email { font-size: 12px; letter-spacing: -0.3px; }
  .contact__icon { width: 11px; height: 11px; margin-top: 4px; flex: none; }

  .front-band { position: absolute; left: 0; bottom: 0; width: 100%; height: 16px; background: linear-gradient(90deg, var(--brand-green), var(--brand-green-light)); border-top: 3px solid var(--paper); }
  .front-band::before { content: ""; position: absolute; left: 0; top: -5px; width: 100%; height: 2px; background: var(--brand-red); }

  .card--back-white .wordmark { left: 0; right: 0; top: 140px; justify-content: center; color: var(--brand-green); font-size: 30px; }
  .card--back-white .wordmark__square { width: 20px; height: 20px; background: var(--brand-red); }

  .card--back-green .wordmark, .card--back-red .wordmark { left: 0; right: 0; top: 150px; justify-content: center; color: var(--paper); font-size: 30px; }
  .card--back-green .wordmark__square, .card--back-red .wordmark__square { width: 20px; height: 20px; background: var(--paper); }

  .web {
    position: absolute; left: 0; right: 0; text-align: center;
    font-family: "Exo 2", "Open Sans", sans-serif; font-weight: 500;
    font-size: 13px; letter-spacing: 3px; white-space: nowrap;
  }
  .card--back-white .web { top: 251px; color: var(--ink); }
  .web__accent-red { color: var(--brand-red); }
  .web__accent-green { color: var(--brand-green); }
  .card--back-green .web, .card--back-red .web { top: 254px; color: var(--paper); }
</style>
</head>
<body>

  <section class="card card--front">
    <div class="wordmark">
      <span class="wordmark__square"></span>
      <span class="wordmark__name">Brisk Property Developments</span>
    </div>
    <div class="divider"></div>
    <div class="contact">
      <p class="contact__name">Lionel Brisk</p>
      <p class="contact__role">Manager/Director</p>
      <p class="contact__row">
        <svg class="contact__icon" viewBox="0 0 12 12" aria-hidden="true"><path fill="#e0232f" d="M2.4 0.6l2 2.2-1.1 1.4c.7 1.6 2 2.9 3.6 3.6l1.4-1.1 2.2 2-1.3 2.1C5 10.6 1.4 7 .3 2z"/></svg>
        <span>0491 638 205</span>
      </p>
      <p class="contact__row contact__row--email">
        <svg class="contact__icon" viewBox="0 0 12 12" aria-hidden="true"><rect x="0" y="2" width="12" height="8" fill="#e0232f"/><path d="M0 2l6 4.5L12 2" fill="none" stroke="#fff" stroke-width="1"/></svg>
        <span>lionel@briskpropertydevelopments.com</span>
      </p>
      <p class="contact__row">
        <svg class="contact__icon" viewBox="0 0 12 12" aria-hidden="true"><path fill="#e0232f" d="M6 0.5L0 6h1.8v5.5h3V8h2.4v3.5h3V6H12z"/></svg>
        <span>Po Box 5347<br>Marlow Ridge , Wyn</span>
      </p>
    </div>
    <div class="front-band"></div>
  </section>

  <section class="card card--back-white">
    <div class="wordmark">
      <span class="wordmark__square"></span>
      <span class="wordmark__name">Brisk Property Developments</span>
    </div>
    <p class="web">www.<span class="web__accent-red">brisk</span><span class="web__accent-green">propertydevelopments</span>.com</p>
  </section>

  <section class="card card--back-green">
    <div class="wordmark">
      <span class="wordmark__square"></span>
      <span class="wordmark__name">Brisk Property Developments</span>
    </div>
    <p class="web">www.briskpropertydevelopments.com</p>
  </section>

  <section class="card card--back-red">
    <div class="wordmark">
      <span class="wordmark__square"></span>
      <span class="wordmark__name">Brisk Property Developments</span>
    </div>
    <p class="web">www.briskpropertydevelopments.com</p>
  </section>

</body>
</html>
```